Business Card Design for Software Development Company

I am looking for a business card design the incorporates my new logo (attached below).

Key information to include:
Name: Martin Quelbrook
Title: CEO
Email: martin@brightwellcivic.example
Phone: 555-218-9403
Website: www.brightwellcivic.example

NOTE: This design should be easy to edit so that we can order cards for different members of our team.

```html
<!DOCTYPE html>
<html lang="en">
<head>
<meta charset="utf-8">
<title>Brightwell Labs – Business Card</title>
<link href="https://fonts.googleapis.com/css2?family=Poppins:wght@400;500;600;800&display=swap" rel="stylesheet">
<style>
  :root {
    --page-bg: #161616;
    --card-top: #2e4556;
    --card-bottom: #34505f;
    --ink-light: #ffffff;
    --teal: #14b1a0;
    --orange: #e9812a;
    --red: #c0332a;
    --muted: #e6ecef;
  }
  * { box-sizing: border-box; margin: 0; padding: 0; }
  html, body { width: 900px; height: 1200px; overflow: hidden; }
  body {
    background: var(--page-bg);
    font-family: "Poppins", sans-serif;
    color: var(--ink-light);
    position: relative;
  }
  .card {
    position: absolute;
    left: 135px;
    width: 630px;
    height: 360px;
    background: linear-gradient(135deg, var(--card-top), var(--card-bottom));
    box-shadow: 0 10px 24px rgba(0,0,0,0.5);
  }
  .card--front { top: 213px; }
  .card--back { top: 627px; }

  .wordmark {
    position: absolute;
    right: 42px;
    text-align: right;
  }
  .wordmark__name {
    display: flex;
    align-items: center;
    justify-content: flex-end;
    gap: 10px;
    font-weight: 600;
    line-height: 1;
    color: var(--ink-light);
    white-space: nowrap;
  }
  .wordmark__mark {
    display: inline-block;
    background: var(--orange);
  }
  .wordmark__tagline {
    font-weight: 600;
    letter-spacing: 0.04em;
    text-transform: uppercase;
    margin-top: 4px;
  }
  .card--front .wordmark { bottom: 38px; }
  .card--front .wordmark__name { font-size: 44px; }
  .card--front .wordmark__mark { width: 30px; height: 30px; }
  .card--front .wordmark__tagline { font-size: 6px; }

  .card--back .wordmark { top: 42px; }
  .card--back .wordmark__name { font-size: 32px; }
  .card--back .wordmark__mark { width: 22px; height: 22px; }
  .card--back .wordmark__tagline { font-size: 5px; }

  .contact {
    position: absolute;
    left: 44px;
    top: 188px;
  }
  .contact__name {
    font-size: 24px;
    font-weight: 800;
    line-height: 1.1;
    background: linear-gradient(180deg, var(--teal) 0%, var(--teal) 50%, var(--orange) 60%, var(--red) 100%);
    -webkit-background-clip: text;
    background-clip: text;
    color: transparent;
  }
  .contact__title {
    font-size: 14px;
    font-weight: 400;
    margin-top: 2px;
  }
  .contact__rule {
    width: 30px;
    height: 2px;
    margin-top: 4px;
    background: linear-gradient(90deg, var(--teal), var(--orange));
  }
  .contact__list {
    list-style: none;
    margin-top: 8px;
  }
  .contact__item {
    display: flex;
    align-items: center;
    gap: 5px;
    font-size: 15px;
    font-weight: 400;
    color: var(--muted);
    height: 24px;
  }
  .contact__item--phone { letter-spacing: 0.22em; }
  .contact__icon { width: 15px; height: 15px; flex: none; }
</style>
</head>
<body>
  <section class="card card--front" aria-label="Card front">
    <div class="wordmark">
      <div class="wordmark__name"><span class="wordmark__mark"></span>Brightwell Labs</div>
      <div class="wordmark__tagline">A division of Brightwell Civic</div>
    </div>
  </section>

  <section class="card card--back" aria-label="Card back">
    <div class="wordmark">
      <div class="wordmark__name"><span class="wordmark__mark"></span>Brightwell Labs</div>
      <div class="wordmark__tagline">A division of Brightwell Civic</div>
    </div>

    <div class="contact">
      <h1 class="contact__name">Martin Quelbrook</h1>
      <p class="contact__title">CEO</p>
      <div class="contact__rule"></div>
      <ul class="contact__list">
        <li class="contact__item contact__item--phone">
          <svg class="contact__icon" viewBox="0 0 24 24" aria-hidden="true">
            <path fill="#d9452b" d="M6.6 10.8a15.1 15.1 0 0 0 6.6 6.6l2.2-2.2c.3-.3.7-.4 1-.2 1.1.4 2.3.6 3.6.6.6 0 1 .4 1 1V20c0 .6-.4 1-1 1A17 17 0 0 1 3 4c0-.6.4-1 1-1h3.5c.6 0 1 .4 1 1 0 1.3.2 2.5.6 3.6.1.3 0 .7-.2 1z"/>
          </svg>
          555-218-9403
        </li>
        <li class="contact__item">
          <svg class="contact__icon" viewBox="0 0 24 24" aria-hidden="true">
            <rect x="2" y="5" width="20" height="14" fill="#e9812a"/>
            <path d="M2 5l10 8 10-8" fill="none" stroke="#c0332a" stroke-width="2"/>
          </svg>
          martin@brightwellcivic.example
        </li>
        <li class="contact__item">
          <svg class="contact__icon" viewBox="0 0 24 24" aria-hidden="true">
            <circle cx="12" cy="12" r="9" fill="none" stroke="#d9452b" stroke-width="2"/>
            <ellipse cx="12" cy="12" rx="4" ry="9" fill="none" stroke="#d9452b" stroke-width="1.6"/>
            <path d="M3 12h18M5 7h14M5 17h14" stroke="#d9452b" stroke-width="1.4"/>
          </svg>
          www.brightwellcivic.example
        </li>
      </ul>
    </div>
  </section>
</body>
</html>
```